Website design for legal tech start up in Switzerland (B2B)

We are for a legal tech start up in Switzerland called KOVA. We have been running since August 2016. This will be our first live website.

We need a website designed and business card design for our start-up in Switzerland. We also need the Web design to be converted into HTML and CSS files.

Function of website:
• To inform potential customers of our services
• Form a key part of our digital marketing and sales footprint.
• Branding

Please find attached logo.
Updates

Project Deadline Extended Reason: Giving us time to review submissions and provide opportunity for more submissions. Added Thursday, February 16, 2017

Project Deadline Extended
Reason: Looking for more idea's not necessarily set on blue and grey colours only.

Target Market(s)

B2B tech powered legal services.

Industry/Entity Type

Legal

Contact Information for Business Card

Lean and slick design.

Coding

Coded - Design and coding required

Number of Pages Required

5+ page

Requirements
Must have
• VERY LEAN AND CLEAN DESIGN!
• We have received many great standard designs, but we are looking for something more out-of-the box: You can get inspiration from these designs: http://www.pixelvane.com/websites/clean/
• Thanks!!
• Easy content management system
• Well structured coding for additional development
• Responsive webpage for all types of devices
• SEO optimized
• Tabs (Home, services, team, careers, blog, contact us)
• Colour scheme complementary to logo
Nice to have
• Look and Design - Approachable, High-tech, Modern
• Easy to add chat bot capability in future
Should not have
• Too busy/ too much clutter
• Not take to long to load

```html
<!DOCTYPE html>
<html lang="en">
<head>
<meta charset="utf-8">
<title>KOVA — Careers, Clients, Blog</title>
<link rel="stylesheet" href="https://fonts.googleapis.com/css2?family=Josefin+Sans:wght@600;700&family=Questrial&display=swap">
<style>
:root{
  --accent:#d9302a;
  --ink:#555;
  --ink-dark:#444;
  --panel:#f4f4f4;
  --frame:#9a9a9a;
  --rule:#dddddd;
  --bg:#ffffff;
}
*{box-sizing:border-box;margin:0;padding:0}
html,body{width:1034px;height:1200px;overflow:hidden;background:var(--bg)}
body{font-family:"Questrial",sans-serif;color:var(--ink)}
.page{position:absolute;left:0;top:0;width:1172px;height:1360px;transform:scale(0.8823);transform-origin:0 0}
.abs{position:absolute}
.section-title{font-family:"Josefin Sans",sans-serif;font-weight:700;color:var(--accent);font-size:19px;letter-spacing:2px;text-align:center;width:100%;left:0}
.section-lede{font-size:14px;letter-spacing:.6px;text-align:center;width:100%;left:0}
.careers-title{top:-2px}
.careers-lede{top:43px}
.slider{top:85px;left:0;width:1170px;height:350px}
.slider-photo{left:0;top:0;width:586px;height:350px;background:linear-gradient(120deg,#d9c9b0 0%,#8a7a68 30%,#2c3038 55%,#c9b8a4 80%,#b94a3c 100%)}
.slider-panel{left:586px;top:0;width:584px;height:350px;background:var(--panel)}
.job-title{left:114px;top:85px;font-family:"Josefin Sans",sans-serif;font-weight:700;color:var(--accent);font-size:17px;letter-spacing:2px}
.job-rule{left:114px;top:115px;width:46px;height:2px;background:#888}
.job-text{left:114px;top:138px;width:300px;font-size:13.5px;line-height:17px;letter-spacing:.6px}
.btn-outline{left:114px;top:234px;width:141px;height:41px;border:1px solid #666;border-radius:2px;font-family:"Josefin Sans",sans-serif;font-weight:700;font-size:14px;letter-spacing:2px;color:var(--ink-dark);display:flex;align-items:center;justify-content:center;padding-top:3px}
.dots{left:565px;top:333px;display:flex;gap:5px}
.dot{width:10px;height:10px;border-radius:50%;border:1.5px solid #888}
.dot.is-active{background:#999;border-color:#999}
.clients-title{top:524px}
.clients-lede{top:564px;font-size:15.5px}
.client{top:616px;width:247px;height:147px;border:2px solid var(--frame);display:flex;align-items:center;justify-content:center;gap:10px;font-family:"Questrial",sans-serif;font-size:26px;color:#4a4a4a;letter-spacing:1px}
.client-mark{width:22px;height:22px;background:#4a4a4a}
.client-mark.round{border-radius:50%}
.divider{left:2px;top:847px;width:1170px;height:1px;background:var(--rule)}
.blog-title{top:929px}
.blog-lede{top:972px}
.post{top:1018px;width:330px}
.post-image{width:330px;height:206px}
.post-title{margin-top:36px;font-family:"Josefin Sans",sans-serif;font-weight:700;font-size:13.5px;color:var(--accent);letter-spacing:.3px}
.post-meta{margin-top:8px;font-size:12px;letter-spacing:1px;color:var(--ink-dark)}
.post-text{margin-top:12px;font-size:13.5px;line-height:17px;letter-spacing:.6px}
</style>
</head>
<body>
<main class="page">
  <section class="careers">
    <h2 class="abs section-title careers-title">CAREERS</h2>
    <p class="abs section-lede careers-lede">Lorem Ipsum is simply dummy text of the printing and typesetting industry. Lorem Ipsum has been the standard dummy text.</p>
    <div class="abs slider">
      <div class="abs slider-photo" role="img" aria-label="Photo of two businessmen in suits in an office"></div>
      <div class="abs slider-panel">
        <h3 class="abs job-title">SENIOR TAX CONSULTANT</h3>
        <span class="abs job-rule"></span>
        <p class="abs job-text">Lorem Ipsum is simply dummy text of the printing and typesetting industry. Lorem Ipsum has been the standard dummy text.</p>
        <a class="abs btn-outline">FIND MORE</a>
      </div>
      <div class="abs dots"><span class="dot is-active"></span><span class="dot"></span><span class="dot"></span></div>
    </div>
  </section>

  <section class="clients">
    <h2 class="abs section-title clients-title">CLIENTS</h2>
    <p class="abs section-lede clients-lede">Most of our clients and partners think we're awesome !</p>
    <div class="abs client" style="left:56px">Northmark</div>
    <div class="abs client" style="left:326px"><span class="client-mark"></span>Loyalwheel</div>
    <div class="abs client" style="left:597px">Answerpoint</div>
    <div class="abs client" style="left:867px"><span class="client-mark round"></span>Carvista</div>
  </section>

  <hr class="abs divider" style="border:0">

  <section class="blog">
    <h2 class="abs section-title blog-title">LATEST FROM OUR BLOG</h2>
    <p class="abs section-lede blog-lede">Lorem Ipsum is simply dummy text of the printing and typesetting industry. Lorem Ipsum has been the standard dummy text.</p>
    <article class="abs post" style="left:71px">
      <div class="post-image" role="img" aria-label="Photo of branded business cards on a pale mint surface" style="background:linear-gradient(135deg,#cfe3dc 0%,#f2f2ee 40%,#b69a78 75%,#cfe0d9 100%)"></div>
      <h3 class="post-title">STANDARD POST WITH PICTURE</h3>
      <p class="post-meta">POSTED BY ADMIN | 22 SEPTEMBER 2016</p>
      <p class="post-text">Lorem Ipsum is simply dummy text of the printing and typesetting industry. Lorem Ipsum has been the standard dummy text.</p>
    </article>
    <article class="abs post" style="left:420px">
      <div class="post-image" role="img" aria-label="Photo of a baguette wrapped in dark branded paper" style="background:linear-gradient(160deg,#d7e6df 0%,#c9a16a 35%,#3a3a3c 60%,#2b2b2d 100%)"></div>
      <h3 class="post-title">STANDARD POST WITH PICTURE</h3>
      <p class="post-meta">POSTED BY ADMIN | 22 SEPTEMBER 2016</p>
      <p class="post-text">Lorem Ipsum is simply dummy text of the printing and typesetting industry. Lorem Ipsum has been the standard dummy text.</p>
    </article>
    <article class="abs post" style="left:769px">
      <div class="post-image" role="img" aria-label="Photo of a wine bottle with a white label and a small plant sprig" style="background:linear-gradient(120deg,#e6e6e4 0%,#cfcfcc 35%,#f4f4f2 55%,#1c1c1c 85%)"></div>
      <h3 class="post-title">STANDARD POST WITH PICTURE</h3>
      <p class="post-meta">POSTED BY ADMIN | 22 SEPTEMBER 2016</p>
      <p class="post-text">Lorem Ipsum is simply dummy text of the printing and typesetting industry. Lorem Ipsum has been the standard dummy text.</p>
    </article>
  </section>
</main>
</body>
</html>
```